Need a cover for eBook:
Title is: 52 Blunders That Sink Your Indie-Released eBook.
Remarks about the title: I know that is difficult to design a cover with a number. You can add the word TOP (in caps or not) before 69 mistakes. It is not mandatory to insert the word TOP. It is up to you if you think you can create a better cover.
Subtitle is: A Starter's Handbook for Releasing Solo, Arranging Pictures and Words, Planning Pages, Raising Signups and Moving More Copies
Author: Walter P. Brenshaw
Publisher: Quillmark Works
The book made the presentation of errors that can occur during the production of an ebook. Title must be big, the title should be readable even when the image is reduced in size. No photo please.
I join my projects as an example. Do what you want but I need impact.

Target Market(s)

Book to sell first at Borvela Reader Shop. Target is authors, men or women, who want to produce ebooks.

Industry/Entity Type

Publishing Company

Font styles to use
Sans Serif

Colors
3176b5
9bcb3c

Requirements
Must have
• High readability when cover is small.
• Here is the definition of the word KILL
• put an end to or cause the failure or defeat of (something).
• "the committee voted to kill the project"
• synonyms: destroy, put an end to, end, extinguish, dash, quash, ruin, wreck, shatter, smash, crush, scotch, thwart; informalput the kibosh on, stymie, scuttle
• "this would kill all hopes of progress"
• veto, defeat, vote down, rule against, reject, throw out, overrule, overturn, put a stop to, quash, squash
• "an opposition attempt to kill the bill"
Nice to have
• I suggested 2 colors but you can you use another one or two. I want cover that sell. There is so bright ideas here. Come on down!
Should not have
• No picture or photo. If a photo or an object had power to the cover, you can insert one. I don't want a photo-collage.

```html
<!DOCTYPE html>
<html lang="en">
<head>
<meta charset="utf-8">
<title>52 Blunders That Sink Your Indie-Released eBook</title>
<link rel="stylesheet" href="https://fonts.googleapis.com/css2?family=Anton&family=Rubik+Mono+One&family=Libre+Baskerville:wght@700&display=swap">
<style>
  :root {
    --magenta: #ec008c;
    --yellow: #fff200;
    --sky: #00aeef;
    --sky-dark: #005f8a;
    --burst: #3a74b4;
    --burst-edge: #e8204a;
    --ink: #111111;
    --paper: #ffffff;
  }
  html, body {
    margin: 0;
    padding: 0;
    overflow: hidden;
    background: var(--paper);
  }
  .cover {
    position: relative;
    width: 927px;
    height: 1200px;
    overflow: hidden;
    background: var(--magenta);
  }
  .cover__backdrop,
  .cover__burst {
    position: absolute;
    left: 0;
    top: 0;
  }
  .title-number,
  .title-word {
    position: absolute;
    left: 0;
    width: 927px;
    margin: 0;
    text-align: center;
    color: var(--sky);
    -webkit-text-stroke: 2px var(--sky-dark);
    text-shadow:
      -2px -2px 0 #7fdcff,
      2px 2px 0 #0076a8,
      4px 4px 0 #00557a,
      6px 7px 6px rgba(0, 0, 0, 0.45);
    line-height: 1;
  }
  .title-number {
    top: 40px;
    font-family: "Rubik Mono One", sans-serif;
    font-size: 186px;
    letter-spacing: 6px;
    padding-left: 14px;
  }
  .title-word {
    top: 236px;
    font-family: "Anton", sans-serif;
    font-size: 150px;
    letter-spacing: 1px;
    padding-left: 22px;
  }
  .title-tail {
    position: absolute;
    top: 416px;
    left: 0;
    width: 927px;
    margin: 0;
    padding-left: 30px;
    box-sizing: border-box;
    text-align: center;
    font-family: "Anton", sans-serif;
    font-size: 70px;
    line-height: 71px;
    color: var(--ink);
    -webkit-text-stroke: 1px var(--paper);
    text-shadow: 0 0 2px var(--paper), 2px 2px 0 var(--paper), -2px -2px 0 var(--paper), 2px -2px 0 var(--paper), -2px 2px 0 var(--paper);
  }
  .subtitle {
    position: absolute;
    top: 786px;
    left: 101px;
    margin: 0;
    font-family: "Libre Baskerville", serif;
    font-weight: 700;
    font-size: 25.5px;
    line-height: 39px;
    color: var(--ink);
  }
  .burst-text {
    position: absolute;
    top: 832px;
    left: 540px;
    width: 240px;
    margin: 0;
    text-align: center;
    font-family: "Libre Baskerville", serif;
    font-weight: 700;
    color: var(--ink);
  }
  .burst-text__small {
    display: block;
    font-size: 25px;
    line-height: 30px;
  }
  .burst-text__accent {
    display: block;
    font-size: 40px;
    line-height: 48px;
    color: var(--magenta);
  }
  .author,
  .publisher {
    position: absolute;
    top: 1086px;
    margin: 0;
    font-family: "Anton", sans-serif;
    font-size: 35px;
    line-height: 44px;
    color: var(--ink);
    letter-spacing: 0.5px;
  }
  .author { left: 70px; }
  .publisher { left: 620px; }
</style>
</head>
<body>
<main class="cover">
  <svg class="cover__backdrop" width="927" height="1200" viewBox="0 0 927 1200" aria-hidden="true">
    <polygon points="0,592 927,973 927,1200 0,1200" fill="var(--yellow)"/>
  </svg>

  <svg class="cover__burst" width="927" height="1200" viewBox="0 0 927 1200" aria-hidden="true">
    <polygon
      points="778,732 733,845 925,870 732,932 790,1050 660,966 610,1160 568,982 470,1040 520,945 390,910 525,860 482,770 590,822 655,760 680,832"
      fill="var(--burst)" stroke="var(--burst-edge)" stroke-width="2" stroke-linejoin="miter"/>
  </svg>

  <h1 class="title">
    <span class="title-number">52</span>
    <span class="title-word">Blunders</span>
    <span class="title-tail">That Sink Your<br>Indie-Released<br>eBook</span>
  </h1>

  <p class="subtitle">A Starter's Handbook for<br>Releasing Solo, Arranging<br>Pictures and Words,<br>Planning Pages,<br>Raising Signups</p>

  <p class="burst-text">
    <span class="burst-text__small">and</span>
    <span class="burst-text__accent">Moving</span>
    <span class="burst-text__small">More Copies</span>
  </p>

  <p class="author">Walter P. Brenshaw</p>
  <p class="publisher">Quillmark Works</p>
</main>
</body>
</html>
```